ready mix concrete business

i need a logo for a ready mix company
it is called Lower Tenbrook Concrete for business cards and promotional items. would like a ready mix truck on it
and must look profesional

```html
<!DOCTYPE html>
<html lang="en">
<head>
<meta charset="utf-8">
<title>Lower Tenbrook Concrete – Business Card</title>
<link rel="stylesheet" href="https://fonts.googleapis.com/css2?family=Montserrat:wght@300;400;600;700&display=swap">
<style>
  :root {
    --card-light: #e2e5e7;
    --logo-backdrop: #9fa2a5;
    --panel-grey: #aeb1b4;
    --brand-blue: #1b72c2;
    --icon-dark: #6f7276;
    --text-white: #ffffff;
  }
  html, body {
    margin: 0;
    width: 1200px;
    height: 826px;
    overflow: hidden;
    background: var(--card-light);
  }
  .business-card {
    position: relative;
    width: 1200px;
    height: 826px;
    font-family: "Montserrat", sans-serif;
    overflow: hidden;
  }
  .card-shapes {
    position: absolute;
    inset: 0;
  }
  .brand-name {
    position: absolute;
    left: 0;
    right: 0;
    top: 170px;
    text-align: center;
    color: var(--brand-blue);
    font-family: "Montserrat", sans-serif;
    font-weight: 700;
    font-size: 66px;
    line-height: 1.15;
    letter-spacing: 2px;
    margin: 0;
  }
  .holder {
    position: absolute;
    left: 70px;
    top: 596px;
    display: flex;
    align-items: center;
    gap: 22px;
    color: var(--text-white);
  }
  .holder-avatar {
    width: 84px;
    height: 84px;
    flex: none;
  }
  .holder-name {
    font-size: 30px;
    font-weight: 400;
    margin: 0;
    letter-spacing: 1px;
  }
  .holder-role {
    font-size: 20px;
    font-weight: 300;
    margin: 2px 0 0;
  }
  .contact-list {
    position: absolute;
    left: 800px;
    top: 548px;
    margin: 0;
    padding: 0;
    list-style: none;
    color: var(--text-white);
    font-size: 18px;
    font-weight: 300;
    line-height: 1.2;
  }
  .contact-item {
    display: flex;
    align-items: center;
    gap: 14px;
    min-height: 24px;
    margin-bottom: 8px;
  }
  .contact-item:last-child {
    align-items: flex-start;
    margin-bottom: 0;
  }
  .contact-icon {
    width: 24px;
    height: 24px;
    flex: none;
  }
  .website {
    position: absolute;
    left: 540px;
    top: 752px;
    color: var(--text-white);
    font-size: 34px;
    font-weight: 400;
    letter-spacing: 1px;
  }
</style>
</head>
<body>
<main class="business-card">
  <svg class="card-shapes" width="1200" height="826" viewBox="0 0 1200 826" aria-hidden="true">
    <rect class="card-base" width="1200" height="826" fill="var(--card-light)"/>
    <polygon class="logo-backdrop" points="250,70 950,70 1015,450 185,450" fill="var(--logo-backdrop)"/>
    <polygon class="info-panel" points="0,560 600,470 1200,560 1200,826 0,826" fill="var(--panel-grey)"/>
    <polyline class="panel-edge" points="0,552 600,462 1200,552" fill="none" stroke="var(--brand-blue)" stroke-width="12"/>
    <path class="footer-band" d="M0,740 Q600,690 1200,715 L1200,826 L0,826 Z" fill="var(--brand-blue)"/>
  </svg>

  <h1 class="brand-name">LOWER TENBROOK<br>CONCRETE</h1>

  <div class="holder">
    <svg class="holder-avatar" viewBox="0 0 84 84" aria-hidden="true">
      <circle cx="42" cy="42" r="38" fill="var(--icon-dark)" stroke="var(--text-white)" stroke-width="4"/>
      <circle cx="42" cy="32" r="11" fill="var(--text-white)"/>
      <path d="M22,62 Q22,46 42,46 Q62,46 62,62 Z" fill="var(--text-white)"/>
    </svg>
    <div>
      <p class="holder-name">YOUR NAME</p>
      <p class="holder-role">Post</p>
    </div>
  </div>

  <ul class="contact-list">
    <li class="contact-item">
      <svg class="contact-icon" viewBox="0 0 24 24" aria-hidden="true"><circle cx="12" cy="12" r="12" fill="var(--icon-dark)"/><path d="M8,6 L10,6 L11,9 L9.5,10.5 Q11,13.5 13.5,14.5 L15,13 L18,14 L18,16 Q17,18 15,18 Q8,16 6,9 Q6,7 8,6 Z" fill="var(--text-white)"/></svg>
      <span>123 456 7890</span>
    </li>
    <li class="contact-item">
      <svg class="contact-icon" viewBox="0 0 24 24" aria-hidden="true"><circle cx="12" cy="12" r="12" fill="var(--icon-dark)"/><rect x="8" y="5" width="8" height="14" rx="1.5" fill="var(--text-white)"/><rect x="9.5" y="7" width="5" height="8" fill="var(--icon-dark)"/></svg>
      <span>123 456 7890</span>
    </li>
    <li class="contact-item">
      <svg class="contact-icon" viewBox="0 0 24 24" aria-hidden="true"><circle cx="12" cy="12" r="12" fill="var(--icon-dark)"/><rect x="6" y="8" width="12" height="8" fill="var(--text-white)"/><polyline points="6,8 12,13 18,8" fill="none" stroke="var(--icon-dark)" stroke-width="1.2"/></svg>
      <span>yourname@mailbox.com</span>
    </li>
    <li class="contact-item">
      <svg class="contact-icon" viewBox="0 0 24 24" aria-hidden="true"><circle cx="12" cy="12" r="12" fill="var(--icon-dark)"/><path d="M12,5 Q17,5 17,10 Q17,13 12,19 Q7,13 7,10 Q7,5 12,5 Z" fill="var(--text-white)"/><circle cx="12" cy="10" r="2" fill="var(--icon-dark)"/></svg>
      <span>1234, Street Name,<br>City</span>
    </li>
  </ul>

  <div class="website">yourwebsite.com</div>
</main>
</body>
</html>
```